Exclusive beauty salon needs a price list or services booklet

I need a new very attractive flyer for my beauty salon, containing information on the different services and their prices.
In attachment you can find a pdf of the "old" one, but I'd love to have a beautifully designed new one!
I'd love to have a booklet in format 148 x 148 mm, or in US format, containing 12 or 16 pages, but if you can offer other nice looking designs they are welcome!
The services that need to come in the booklet with their prices can all be found on my website: www.atelierverano.be, starting with
Gelaatsverzorging
Wimperverlenging
Suikerontharing
Wimperlifting
Permanente Make Up
Airbrush Tanning

Target Market(s)

woman from 20 to 89 years old

Industry/Entity Type

Beauty Salon

Font styles to use
Sans Serif

Colors

Designer to choose colors to be used in the design.

Requirements
Must have
• a classy nice look, it must contain details about the services from my beauty salon and their prices, and nice pictures.
• The Names, prices and explanations of the services can easily be found on my website: www.atelierverano.be
Nice to have
• In attachment you can find the "old" price list in pdf, what I need now is a "new booklet" with the new logo and updated services price list.
• I need a very nice and attractive looking booklet, classy chique, Paris chique, looking very expensive.
Should not have
• Not too much colors, not too curly, but still feminine

```html
<!DOCTYPE html>
<html lang="nl">
<head>
<meta charset="utf-8">
<title>Wimperlifting Lumelift Lashes – Atelier Verano</title>
<link rel="stylesheet" href="https://fonts.googleapis.com/css2?family=Questrial&display=swap">
<style>
  :root{
    --backdrop:#a7a7a7;
    --paper:#ffffff;
    --paper-shade:#f1f1f1;
    --text:#8c8c8c;
    --text-strong:#6f6f6f;
    --ink:#1e1e1e;
    --teal:#5fbfc3;
    --band-a:#b7dfec;
    --band-b:#e4f3f8;
    --skin-a:#e9c7b6;
    --skin-b:#d9ab98;
  }
  *{box-sizing:border-box;margin:0;padding:0}
  html,body{width:1200px;height:523px;overflow:hidden}
  body{background:var(--backdrop);font-family:"Questrial",sans-serif;color:var(--text);position:relative}
  .spread{position:absolute;left:128px;top:14px;width:944px;height:495px;display:flex}
  .page{position:relative;width:472px;height:495px;background:var(--paper)}
  .page--left{background:linear-gradient(to right,var(--paper) 92%,var(--paper-shade))}
  .page--right{background:linear-gradient(to left,var(--paper) 92%,var(--paper-shade))}
  .page-title{position:absolute;left:22px;top:20px;font-size:16px;font-weight:400;color:var(--teal);letter-spacing:.2px}
  .brand{position:absolute;left:22px;top:112px;width:110px;display:flex;align-items:center;gap:6px}
  .brand-mark{width:8px;height:8px;background:var(--ink);flex:none}
  .brand-name{font-size:12px;font-weight:400;color:var(--ink);letter-spacing:1px;line-height:1.2}
  .result-photo{position:absolute;left:143px;top:70px;width:310px;height:123px;display:flex;gap:2px}
  .result-photo .frame{flex:1;position:relative;background:linear-gradient(160deg,var(--skin-a),var(--skin-b))}
  .result-photo .label{position:absolute;right:10px;bottom:4px;font-size:7px;color:#fff;font-style:italic;letter-spacing:.5px}
  .formula-band{position:absolute;left:22px;top:200px;width:440px;height:19px;background:linear-gradient(to right,var(--band-a),var(--band-b));color:#fff;font-size:11.5px;line-height:19px;padding-left:24px}
  .copy{position:absolute;font-size:8.5px;line-height:11px}
  .copy p{margin-bottom:11px}
  .copy h3{font-size:8.5px;font-weight:700;color:var(--text-strong)}
  .copy ul{list-style:none;margin-top:-11px;margin-bottom:11px}
  .copy ul:last-child{margin-bottom:0}
  .copy li::before{content:"• "}
  .copy--left{left:22px;top:240px;width:420px}
  .copy--right{left:14px;top:18px;width:442px}
  .salon-mark{position:absolute;right:18px;bottom:22px;display:flex;align-items:center;gap:4px;font-size:7px;color:var(--ink);letter-spacing:1px}
  .salon-mark .dot{width:6px;height:6px;border:1px solid var(--ink)}
</style>
</head>
<body>
<main class="spread">
  <section class="page page--left">
    <h1 class="page-title">WIMPERLIFTING LUMELIFT LASHES</h1>
    <div class="brand">
      <span class="brand-mark"></span>
      <span class="brand-name">LUMELIFT LASHES</span>
    </div>
    <div class="result-photo">
      <div class="frame" role="img" aria-label="Close-up van een oog vóór de wimperlifting"><span class="label">BEFORE</span></div>
      <div class="frame" role="img" aria-label="Close-up van een oog na de wimperlifting"><span class="label">AFTER</span></div>
    </div>
    <div class="formula-band">Lumelift = Length + Volume + Lift voor uw natuurlijke wimpers.</div>
    <div class="copy copy--left">
      <p>Het hebben van mooie, lange en volumineuze wimpers staat hoog op het verlanglijstje van vele vrouwen. Het liefst heeft men de wimpers mooi gelift voor een open blik die de ogen optisch groter maakt. Niet voor niets is mascara één van de best verkochte make-upproducten.</p>
      <p>De nieuwe en revolutionaire Lumelift-methode zorgt echter na slechts 1 behandeling van 60 minuten, gedurende minimaal 6 weken voor Lange, Volumineuze en geLifte wimpers. Dit alles, zonder dat daar een wimperkrultang of dikke lagen mascara aan te pas hoeven te komen!</p>
      <h3>Hoe werkt het?</h3>
      <p>De revolutionaire Lumelift-methode is een behandeling voor de eigen wimpers, waarbij géén gebruik wordt gemaakt van het aanbrengen van valse wimpers.<br>
      Bij deze bijzondere behandeling die volledig nieuw is, wordt een laagje 'coating' aangebracht bij de wimperaanzet met een nieuw soort gelformule. Dan bepalen we aan de hand van uw wimperlengte de curve van het siliconen schildje.<br>
      Door middel van dit siliconen schildje worden de wimpers effectief gelift vanaf de wimperaanzet (dus vanaf de wortel), hetgeen zorgt voor een open blik met lange, volumineuze en perfect gescheiden wimpers.<br>
      Door ook nog een tint nadien toe te voegen, krijgen de wimpers meteen een super color boost!</p>
    </div>
  </section>
  <section class="page page--right">
    <div class="copy copy--right">
      <p>De sessie heeft 24u nodig om te fixeren. Het is dus ook niet aan te raden de behandeling te kort voor het slapen te ondergaan.</p>
      <p>De eerste 24u:</p>
      <ul>
        <li>Geen water aan de ogen</li>
        <li>Geen make-up aan de ogen</li>
        <li>Geen oogcrème</li>
        <li>Niet wrijven in de ogen</li>
        <li>Geen sauna, zwem- of stoombad</li>
      </ul>
      <p>Wimperlifting is een techniek die wimperverbetering en verven combineert, een unieke combinatie!</p>
      <p>Wimperlifting blijft 4 tot 6 weken zitten.</p>
      <ul>
        <li>Je hebt geen mascara of wimperkrultang meer nodig.</li>
        <li>Voelt licht en natuurlijk aan.</li>
        <li>Uw ogen lijken groter.</li>
        <li>De Wimperlift is niet schadelijk voor de eigen wimpers.</li>
        <li>Bestand tegen water, douchen, zweten, tranen, zwemmen en slapen.</li>
      </ul>
      <p>Wat is het verschil tussen Wimperlifting en Wimperpermanent?<br>
      Bij het zetten van wimperpermanent worden er klemmen en/of rollers gebruikt. Door deze methode kan er slechts een gedeelte van de wimpers behandeld worden, waardoor u broze wimpers kunt krijgen en wimperhaartjes afbreken. De Wimperlift daarentegen is totaal niet schadelijk voor uw wimpers!</p>
      <p>U kunt GEEN wimperlift behandeling ondergaan wanneer u:</p>
      <ul>
        <li>een infectie heeft van de Zeis kliertjes (bekend als "een strontje").</li>
        <li>uw wimpers zijn uitgevallen als gevolg van Alopecia of chemotherapie.</li>
        <li>lijdt aan conjunctivitis.</li>
        <li>lijdt aan trichotillomanie.</li>
        <li>zwanger bent of borstvoeding geeft.</li>
        <li>in het verleden last heeft gehad van haaruitval.</li>
        <li>extreem korte of extreem fijne wimpers heeft.</li>
      </ul>
      <p>Wanneer u last heeft van onderstaande aandoeningen is het WEL MOGELIJK om een wimperlift behandeling te ondergaan er wordt dan voorafgaand aan de behandeling een allergietest afgenomen:</p>
      <ul>
        <li>Droge ogen syndroom.</li>
        <li>Wanneer u veel last heeft van allergieën.</li>
      </ul>
    </div>
    <div class="salon-mark"><span class="dot"></span>ATELIER VERANO</div>
  </section>
</main>
</body>
</html>
```